Business Card: RW Office Partners - Your organised problem solver

Business Name: RW Office Partners
Website: www.rwofficepartners.com.au
Email: marisol@rwofficepartners.com.au
Mobile: 61 482 907 236
Facebook: @rwofficepartners
Instrgram: @rwofficepartners

Brading Colours:
HEX
#986474
#ddccd3
#7a8498
#c9d8e4
#000000
#ffffff

Tag Line: Your dependable office ally

Link to DRAFT website:
https://deskhelpcollective.wixsite.com/rw-office-partners

About Page from the website:
My name is Marisol Wrenfield, and I would love to assist you to become more productive in your day to day and achieve your business and personal goals.
My mission is to give you time, time to work on the important tasks of your business or to be able to spend more time with your family. I will take on the tasks you don’t have time for, don’t know well or simply don’t like to do.
I have an extensive background in Administration, Tender Coordination, Document Control, WHS and Quality Management working primarily in the Construction, Mining and Corporate World.
I am passionate about being organised, having order and making things in your life (and mine) easier! I love to watch something unfold and grow into something amazing! I am known for being the go-to problem solver, the organiser of all things, producing high standards of work even under pressure. I’m also a confident communicator, and I understand that you’re busy running your business.

Target Market(s)

Small to Medium Business who require assistance in their business by a virtual assistant.

Industry/Entity Type

Virtual Assistant

Contact Information for Business Card

Mobile: 61 482 907 236

Font styles to use
Sans Serif

Colors
ffffff

Requirements
Must have
• Branding Colours as outlined.
Contact Details as outlined.
Logo as provided.
Proper contact details - mobile, facebook, instragm, website.
Simple, Elegant, very clean looking.
Should not have
• Note cute with pictures.
Not too girly as still want to market to construction companies.

```html
<!DOCTYPE html>
<html lang="en">
<head>
<meta charset="UTF-8">
<title>RW Office Partners – Business Card</title>
<link href="https://fonts.googleapis.com/css2?family=Montserrat:wght@500&family=Roboto:wght@400&display=swap" rel="stylesheet">
<style>
  :root {
    --mauve: #986474;
    --blush: #ddccd3;
    --slate: #7a8498;
    --mist: #c9d8e4;
    --ink: #000000;
    --paper: #ffffff;
    --card: #1d1d1f;
    --stage: #e9e9eb;
  }
  * { margin: 0; padding: 0; box-sizing: border-box; }
  html, body { width: 1200px; height: 900px; overflow: hidden; background: var(--stage); }
  .stage {
    width: 1200px; height: 900px;
    display: flex; flex-direction: column; align-items: center; justify-content: center; gap: 40px;
  }
  .card {
    position: relative;
    width: 640px; height: 366px;
    background: var(--card);
    border-radius: 4px;
    box-shadow: 0 10px 30px rgba(0,0,0,.25);
    overflow: hidden;
  }
  .brand-name {
    font-family: "Montserrat", sans-serif;
    font-weight: 500;
    color: var(--slate);
    text-transform: uppercase;
    letter-spacing: 1px;
    line-height: 1.05;
  }
  /* front */
  .card-front .brand-name {
    position: absolute; left: 46px; top: 70px;
    font-size: 30px; width: 240px;
  }
  .divider {
    position: absolute; left: 300px; top: 150px;
    width: 1px; height: 104px; background: var(--mauve);
  }
  .contact-list {
    position: absolute; left: 318px; top: 150px;
    list-style: none;
    font-family: "Roboto", sans-serif; font-size: 15px; color: var(--paper);
  }
  .contact-list li { display: flex; align-items: center; gap: 8px; height: 26px; white-space: nowrap; }
  .contact-list svg { width: 13px; height: 13px; flex: none; }
  .tagline {
    position: absolute; left: 46px; top: 290px;
    font-family: "Roboto", sans-serif; font-size: 15px; color: var(--paper);
  }
  /* back */
  .pattern-field {
    position: absolute; inset: 0;
    background: linear-gradient(135deg, #232325 0%, #1a1a1c 50%, #232325 100%);
  }
  .card-back .brand-name {
    position: absolute; right: 44px; bottom: 40px;
    font-size: 24px; text-align: left; width: 200px;
  }
</style>
</head>
<body>
<main class="stage">
  <section class="card card-front">
    <div class="brand-name">RW Office Partners</div>
    <div class="divider"></div>
    <ul class="contact-list">
      <li>
        <svg viewBox="0 0 16 16" aria-hidden="true"><path fill="#986474" d="M3.6 1.2 6 3.6 4.6 5.5c.8 2.4 3.1 4.7 5.9 5.9l1.9-1.4 2.4 2.4-1.8 2.4C6.2 14.4 1.6 9.8 1.2 3z"/></svg>
        <span>61 482 907 236</span>
      </li>
      <li>
        <svg viewBox="0 0 16 16" aria-hidden="true"><rect x="1" y="3" width="14" height="10" fill="#986474"/><path d="M1 3l7 6 7-6" fill="none" stroke="#1d1d1f" stroke-width="1.4"/></svg>
        <span>marisol@rwofficepartners.com.au</span>
      </li>
      <li>
        <svg viewBox="0 0 16 16" aria-hidden="true"><circle cx="8" cy="8" r="6.5" fill="none" stroke="#986474" stroke-width="1.6"/><path d="M1.5 8h13M8 1.5c-3 3.5-3 9.5 0 13M8 1.5c3 3.5 3 9.5 0 13" fill="none" stroke="#986474" stroke-width="1.2"/></svg>
        <span>www.rwofficepartners.com.au</span>
      </li>
      <li>
        <svg viewBox="0 0 16 16" aria-hidden="true"><circle cx="8" cy="8" r="6" fill="#7a8498"/></svg>
        <span>@rwofficepartners</span>
      </li>
    </ul>
    <p class="tagline">Your dependable office ally</p>
  </section>

  <section class="card card-back">
    <div class="pattern-field" role="img" aria-label="Subtle tone-on-tone repeating brand pattern"></div>
    <div class="brand-name">RW Office Partners</div>
  </section>
</main>
</body>
</html>
```